I have a logo and need to design the business card and stationery.
Updates

The uploaded logo image named as GREYMARSH CONTRACTS which is to be replaced to GREYMARSH CONTRACTS. Kindly add below details and submit the designs- Company name- Greymarsh Engineering Contracts LLP Name & Post- Kelvan Joshi (Designated Partner) Address- Block No.317, Wing C, Tulvo Trade Court, Manek Pural Road, Ruparel Industrial Estate, Goregaon(E), Mumbai - 400 063 Contact- +91 97415 60382 Email- kelvanjoshi@mailbrook.example Website- www.greymarshcontracts.example Contact for Letterhead- +91-22-28754193

Hi Tovin Rahul, We are liking your Design #28860835. We have suggested some changes which are mentioned in feedback. Kindly revert with it asap to finalize this design.

Colors

Designer to choose colors to be used in the design.

```html
<!DOCTYPE html>
<html lang="en">
<head>
<meta charset="utf-8">
<title>Greymarsh Contracts – Business Card</title>
<link href="https://fonts.googleapis.com/css2?family=Montserrat:wght@400;500;600;700&display=swap" rel="stylesheet">
<style>
  :root {
    --backdrop: #3b3b3b;
    --card-white: #ffffff;
    --ink: #2f2f2f;
    --ink-soft: #4a4a4a;
    --rule: #555555;
    --back-light: #5c5c5c;
    --back-dark: #262626;
    --mark-white: #ffffff;
  }
  * { margin: 0; padding: 0; box-sizing: border-box; }
  html, body {
    width: 1200px; height: 1199px; overflow: hidden;
    background: var(--backdrop);
    font-family: "Montserrat", sans-serif;
  }
  .card {
    position: absolute; left: 237px; width: 726px; height: 415px; overflow: hidden;
  }
  .card--front { top: 143px; background: var(--card-white); }
  .card--back { top: 646px; }

  .brand { position: absolute; left: 45px; top: 128px; width: 310px; text-align: center; color: var(--ink); font-weight: 700; }
  .brand__square { width: 94px; height: 94px; border: 11px solid var(--ink); margin: 0 auto 16px; }
  .brand__name { font-size: 30px; letter-spacing: 1px; line-height: 1; }
  .brand__sub { font-size: 15px; letter-spacing: 12px; margin-top: 8px; margin-right: -12px; line-height: 1; }

  .divider { position: absolute; left: 382px; top: 100px; width: 1.5px; height: 218px; background: var(--rule); }

  .contact { position: absolute; left: 405px; top: 98px; width: 305px; color: var(--ink-soft); }
  .contact__name { font-size: 24px; font-weight: 600; color: var(--ink); letter-spacing: 0.5px; line-height: 1.1; }
  .contact__role { font-size: 14px; letter-spacing: 1px; margin-top: 4px; text-transform: uppercase; }
  .contact__address { font-size: 13.5px; line-height: 19px; margin-top: 10px; letter-spacing: 0.2px; }
  .contact__list { list-style: none; margin-top: 8px; font-size: 13.5px; letter-spacing: 0.2px; }
  .contact__list li { display: flex; align-items: center; gap: 7px; height: 21px; white-space: nowrap; }
  .contact__list svg { width: 11px; height: 11px; flex: none; }

  .back-pattern {
    position: absolute; inset: 0;
    background: linear-gradient(90deg, var(--back-light) 0%, #474747 30%, var(--back-dark) 48%, #2c2c2c 100%);
  }
  .back-mark {
    position: absolute; left: 0; right: 0; top: 172px; text-align: center;
    color: var(--mark-white); font-weight: 700; font-size: 14px; letter-spacing: 2px;
  }
  .back-mark__square { width: 69px; height: 69px; background: var(--mark-white); margin: 0 auto 8px; }
</style>
</head>
<body>
  <section class="card card--front">
    <div class="brand">
      <div class="brand__square"></div>
      <div class="brand__name">GREYMARSH</div>
      <div class="brand__sub">CONTRACTS</div>
    </div>
    <div class="divider"></div>
    <div class="contact">
      <div class="contact__name">KELVAN JOSHI</div>
      <div class="contact__role">Designated Partner</div>
      <div class="contact__address">Block No.317, Wing C, Tulvo Trade Court,<br>Manek Pural Road, Ruparel Industrial<br>Estate, Goregaon(E), Mumbai - 400 063</div>
      <ul class="contact__list">
        <li><svg viewBox="0 0 12 12"><path d="M3 1 L5 3.5 L4 5 Q5 7.5 7 8 L8.5 7 L11 9 L9.5 11 Q2 10 1 2.5 Z" fill="#4a4a4a"/></svg>+91 97415 60382</li>
        <li><svg viewBox="0 0 12 12"><rect x="1" y="2.5" width="10" height="7" fill="none" stroke="#4a4a4a" stroke-width="1.2"/><path d="M1 2.5 L6 6.5 L11 2.5" fill="none" stroke="#4a4a4a" stroke-width="1.2"/></svg>kelvanjoshi@mailbrook.example</li>
        <li><svg viewBox="0 0 12 12"><circle cx="6" cy="6" r="5" fill="none" stroke="#4a4a4a" stroke-width="1"/><ellipse cx="6" cy="6" rx="2.2" ry="5" fill="none" stroke="#4a4a4a" stroke-width="0.9"/><path d="M1 6 H11 M2 3.5 H10 M2 8.5 H10" stroke="#4a4a4a" stroke-width="0.8"/></svg>www.greymarshcontracts.example</li>
      </ul>
    </div>
  </section>

  <section class="card card--back">
    <div class="back-pattern" role="img" aria-label="Repeating brand pattern fading from light grey to dark grey"></div>
    <div class="back-mark">
      <div class="back-mark__square"></div>
      GREYMARSH
    </div>
  </section>
</body>
</html>
```